Bulldog themed background for Real Estate Purchase Letter

I need a phantom background or watermark on a standard 8 1/2" x 11" paper. I am going to put a letter over the background. I want a bulldog theme that is cute, funny and original. This letter is for a real estate project and we want to capture the person sub-consciously . Attached is my personal dogs. If you want to use them you can but not required. I have attached the letter that I am trying to emulate. I want bulldogs not horses.

Target Market(s)

45 years old and higher

Industry/Entity Type

Real Estate

Font styles to use
Serif
Sans Serif

Colors

Designer to choose colors to be used in the design.

Requirements
Must have
• fun, happiness, reassuring,
Should not have
• violence, negativity, unhappy

```html
<!DOCTYPE html>
<html lang="en">
<head>
<meta charset="utf-8">
<title>Closing Letter – Bulldog Background</title>
<link href="https://fonts.googleapis.com/css2?family=Tinos:ital,wght@0,400;1,400&display=swap" rel="stylesheet">
<style>
  :root {
    --mat: #000000;
    --paper: #ffffff;
    --ink: #1a1a1a;
    --grass: #8f8f8f;
    --dog-light: #efe6da;
    --dog-shade: #cbbfb0;
    --collar: #8a3a48;
  }
  html, body {
    margin: 0;
    padding: 0;
    width: 960px;
    height: 1200px;
    overflow: hidden;
    background: var(--mat);
  }
  .letter-page {
    position: absolute;
    left: 219px;
    top: 264px;
    width: 520px;
    height: 671px;
    background: var(--paper);
    overflow: hidden;
    font-family: "Tinos", "Times New Roman", serif;
    font-size: 11.6px;
    line-height: 14px;
    color: var(--ink);
  }
  .phantom-background {
    position: absolute;
    inset: 0;
    width: 520px;
    height: 671px;
  }
  .letter-block {
    position: absolute;
    left: 44px;
    width: 436px;
    margin: 0;
  }
  .date { top: 57px; }
  .recipient { top: 84px; }
  .salutation { top: 140px; }
  .opening { top: 168px; }
  .para-thanks { top: 196px; }
  .para-evaluation { top: 278px; }
  .para-closing { top: 348px; }
  .sign-off { top: 404px; }
  .signature { top: 458px; }
</style>
</head>
<body>
  <main class="letter-page">
    <svg class="phantom-background" viewBox="0 0 520 671" role="img" aria-label="Faded photograph of a smiling white bulldog sitting on grass, used as a soft watermark behind the letter">
      <defs>
        <linearGradient id="grassFade" x1="0" y1="0" x2="0" y2="1">
          <stop offset="0" stop-color="#ffffff" stop-opacity="0"/>
          <stop offset="0.35" stop-color="#d9d9d9" stop-opacity="0.7"/>
          <stop offset="1" stop-color="#8f8f8f"/>
        </linearGradient>
        <radialGradient id="dogTone" cx="0.5" cy="0.55" r="0.6">
          <stop offset="0" stop-color="#efe6da"/>
          <stop offset="0.7" stop-color="#ddd2c4"/>
          <stop offset="1" stop-color="#cbbfb0" stop-opacity="0"/>
        </radialGradient>
        <linearGradient id="topFade" x1="0" y1="0" x2="0" y2="1">
          <stop offset="0" stop-color="#ffffff"/>
          <stop offset="1" stop-color="#ffffff" stop-opacity="0"/>
        </linearGradient>
      </defs>
      <rect x="0" y="420" width="520" height="251" fill="url(#grassFade)"/>
      <ellipse cx="262" cy="470" rx="140" ry="200" fill="url(#dogTone)" opacity="0.85"/>
      <rect x="0" y="250" width="520" height="110" fill="url(#topFade)"/>
    </svg>

    <p class="letter-block date">Date</p>
    <p class="letter-block recipient">Member Name(s)<br>Address<br>City/State/Zip Code</p>
    <p class="letter-block salutation">Dear Name(s):</p>
    <p class="letter-block opening">Congratulations on the closing of your home!</p>
    <p class="letter-block para-thanks">The Harbor Federal HomeStride program would like to take this opportunity to say thank you for allowing our team to assist you with your real estate needs. Our team’s goal was to make your real estate experience as smooth and pleasurable as possible. All members of your real estate team (your Real Estate Agent, and your Harbor Federal Specialist) worked together to ensure that you received the excellent service you are accustomed to from Harbor Federal. We sincerely hope that we were successful!</p>
    <p class="letter-block para-evaluation">In the next few days, you will receive a service evaluation from the Harbor Federal Savings Bank. This is our program’s report card. We are very anxious to hear about your experience using the HomeStride program. Your feedback is extremely valuable! We respectfully request that you take a moment to fill out the evaluation and return it to Harbor Federal.</p>
    <p class="letter-block para-closing">Again, on behalf of the entire HomeStride team, thank you for using the program and selecting (insert real estate firm name). We hope that HomeStride will again be able to serve you with your future real estate needs.</p>
    <p class="letter-block sign-off">Sincerely,</p>
    <p class="letter-block signature">(Insert Principal Name)<br>(Insert Title)</p>
  </main>
</body>
</html>
```